Designer Instructions – Updated Referral Program Flyer

(Based on the mock-up in “Brief Layout and Instructions.pdf”)

OVERALL STYLE + LAYOUT

Maintain the same general layout, structure, and flow as the mock-up flyer (front and back).

This is an update of an older flyer, not a full redesign — keep the same sections, proportions, and overall visual feel, but with cleaner, more modern design improvements.

The final flyer should look clean, bold, professional, and high-impact, geared toward realtors, property managers, and contractors who refer work.

FRONT SIDE INSTRUCTIONS
1. Header Section

Remove the Rebuild Harbor Crest logo from the top banner.
(Shown on page 1 of the PDF)

2. Main Headline

Keep the same three-line structure:
EARN
UNLIMITED
CASH

Center it, maximize impact, and increase the font size of CASH so all three words match in importance.

Make the headline bold, clean, and the main focal point.

3. Cash Incentive Box

Keep the "$500 minimum OR 10% per referral" box, but upgrade the graphics to look sharper and more modern.

Ensure the wording matches exactly what’s in the mock-up.

4. Premier Partner Program Ribbon

Clean up and modernize the "PREMIER PARTNER PROGRAM" bar while keeping the same position and structure.

Ensure the checkmark badge remains crisp and professional.

5. Supporting Icons Section

Keep the four icons/benefit boxes (Guaranteed Payout, Free Evaluations, Affordable Solutions, Industry Leaders) in the same order.

Update the icons to cleaner, more modern styles — but maintain the same meanings.

Improve alignment and spacing for sharper visual consistency.

6. Remove Icons in Contact Area

At the bottom (“CALL TEXT OR BOOK ONLINE 858-471-6093 BrightlaneRenovate.com”), remove the phone and internet icons, as noted on page 2 of the PDF.

7. Replace All Images

I (Dorian) will provide all updated stock images separately via email.

Replace the flood/water-damage imagery and roof leak with the new images I send.

Keep image placement and proportions the same as the mock-up.

BACK SIDE INSTRUCTIONS
1. Header Image + “REFER / EARN” Section

Maintain the same large split-image layout (“The more you refer, the more you earn”).

Replace all background imagery with the new assets I will send.

Keep the CASH FLOW image section but modernize the type and spacing.

2. “HOW IT WORKS” Section

Preserve the three-column layout:

Refer Flood, Water & Mold Damage

We Take Care of Everything (evaluations/insurance)

Get Paid to Share

Update images, tighten spacing, and use modern iconography.

3. Remove Phone/Internet Icons

Same as the front side — remove small communication icons and keep only the text/number/URL.

4. Bottom Contact Bar

Keep the blue bar, same wording, same layout — just modernize the style if needed for clarity.

5. Replace All Back-Side Images

Again, I will email you the image assets.

Keep the layout EXACT — just update with higher-quality photos and improved design.

TEXT CONTENT (Keep as-is unless spacing adjustments needed)

All text shown in the PDF should remain exactly the same unless spacing or visual balance requires minor adjustments.
Example from page 3:

“REFER FLOOD, MOLD & CONSTRUCTION JOBS”

“We Schedule a Free Estimate. If Approved, You Get Paid.”

“Everybody Benefits From Referrals”

Everything stays, just refreshed and visually improved.

DESIGN GOALS

Flyer should look high-end and trustworthy, not salesy.

Consistent color theme: blues, whites, yellows, same palette as original.

Use bold, modern fonts with strong readability.

Ensure all headlines pop and all benefit boxes are clean, well-aligned, and evenly spaced.

The final result should feel like a premium referral program flyer for a top-tier restoration/remodel company.

FILES I WILL PROVIDE

I will send the designer:

All replacement stock photos

Any updated logos (if needed)

Original high-resolution version of the mock-up (if available)

Any additional icons preferred

Colors
0054AA
0677BA
7BADD7
CADEEF
E8F1F8

Requirements
Must have
• Designer Instructions – Updated Referral Program Flyer (Based on the mock-up in “Brief Layout and Instructions.pdf”) OVERALL STYLE + LAYOUT Maintain the same general layout, structure, and flow as the mock-up flyer (front and back). This is an update of an older flyer, not a full redesign — keep the same sections, proportions, and overall visual feel, but with cleaner, more modern design improvements. The final flyer should look clean, bold, professional, and high-impact, geared toward realtors, property managers, and contractors who refer work. FRONT SIDE INSTRUCTIONS 1. Header Section Remove the Rebuild Harbor Crest logo from the top banner. (Shown on page 1 of the PDF) 2. Main Headline Keep the same three-line structure: EARN UNLIMITED CASH Center it, maximize impact, and increase the font size of CASH so all three words match in importance. Make the headline bold, clean, and the main focal point. 3. Cash Incentive Box Keep the "$500 minimum OR 10% per referral" box, but upgrade the graphics to look sharper and more modern. Ensure the wording matches exactly what’s in the mock-up. 4. Premier Partner Program Ribbon Clean up and modernize the "PREMIER PARTNER PROGRAM" bar while keeping the same position and structure. Ensure the checkmark badge remains crisp and professional. 5. Supporting Icons Section Keep the four icons/benefit boxes (Guaranteed Payout, Free Evaluations, Affordable Solutions, Industry Leaders) in the same order. Update the icons to cleaner, more modern styles — but maintain the same meanings. Improve alignment and spacing for sharper visual consistency. 6. Remove Icons in Contact Area At the bottom (“CALL TEXT OR BOOK ONLINE 858-471-6093 BrightlaneRenovate.com”), remove the phone and internet icons, as noted on page 2 of the PDF. 7. Replace All Images I (Dorian) will provide all updated stock images separately via email. Replace the flood/water-damage imagery and roof leak with the new images I send. Keep image placement and proportions the same as the mock-up. BACK SIDE INSTRUCTIONS 1. Header Image + “REFER / EARN” Section Maintain the same large split-image layout (“The more you refer, the more you earn”). Replace all background imagery with the new assets I will send. Keep the CASH FLOW image section but modernize the type and spacing. 2. “HOW IT WORKS” Section Preserve the three-column layout: Refer Flood, Water & Mold Damage We Take Care of Everything (evaluations/insurance) Get Paid to Share Update images, tighten spacing, and use modern iconography. 3. Remove Phone/Internet Icons Same as the front side — remove small communication icons and keep only the text/number/URL. 4. Bottom Contact Bar Keep the blue bar, same wording, same layout — just modernize the style if needed for clarity. 5. Replace All Back-Side Images Again, I will email you the image assets. Keep the layout EXACT — just update with higher-quality photos and improved design. TEXT CONTENT (Keep as-is unless spacing adjustments needed) All text shown in the PDF should remain exactly the same unless spacing or visual balance requires minor adjustments. Example from page 3: “REFER FLOOD, MOLD & CONSTRUCTION JOBS” “We Schedule a Free Estimate. If Approved, You Get Paid.” “Everybody Benefits From Referrals” Everything stays, just refreshed and visually improved. DESIGN GOALS Flyer should look high-end and trustworthy, not salesy. Consistent color theme: blues, whites, yellows, same palette as original. Use bold, modern fonts with strong readability. Ensure all headlines pop and all benefit boxes are clean, well-aligned, and evenly spaced. The final result should feel like a premium referral program flyer for a top-tier restoration/remodel company. FILES I WILL PROVIDE I will send the designer: All replacement stock photos Any updated logos (if needed) Original high-resolution version of the mock-up (if available) Any additional icons preferred

```html
<!DOCTYPE html>
<html lang="en">
<head>
<meta charset="utf-8">
<title>Partner Referral Program Flyer</title>
<link href="https://fonts.googleapis.com/css2?family=Montserrat:wght@400;500;600;700;800;900&display=swap" rel="stylesheet">
<style>
:root{
  --navy:#1c3f7c;
  --navy-deep:#14306a;
  --blue:#0054aa;
  --sky:#2aa5d9;
  --mist:#cadeef;
  --ice:#e8f1f8;
  --yellow:#f5c518;
  --amber:#f29a1f;
  --ink:#1c3f7c;
  --paper:#ffffff;
  --stage:#dcdcdc;
  --numeral:#e3e6ec;
  --line:#c9d2e0;
}
*{box-sizing:border-box;margin:0;padding:0}
html,body{width:1200px;height:960px;overflow:hidden;background:var(--stage)}
body{font-family:"Montserrat",sans-serif;color:var(--ink);position:relative}
.flyer{position:absolute;top:111px;width:570px;height:738px;background:var(--paper);overflow:hidden;box-shadow:0 10px 30px rgba(0,0,0,.15)}
.flyer--back{left:20px}
.flyer--front{left:610px}

/* contact bar */
.contact-bar{position:absolute;left:0;right:0;bottom:0;height:86px;background:var(--navy);color:#fff;text-align:center;padding-top:14px}
.contact-bar__label{font-size:12px;font-weight:600;letter-spacing:.06em}
.contact-bar__phone{font-size:30px;font-weight:800;line-height:1.1;letter-spacing:.01em}
.contact-bar__url{font-size:11px;font-weight:500;color:var(--yellow);margin-top:2px}

/* back side hero */
.hero{position:absolute;left:0;top:0;width:570px;height:272px}
.hero__money{position:absolute;left:0;top:140px;width:570px;height:132px;background:linear-gradient(135deg,#c9d3d6,#e9eeee 40%,#b9c8c5 70%,#dfe5e4)}
.hero__team{position:absolute;left:0;top:0;width:300px;height:170px;background:linear-gradient(180deg,#a7b8cc,#5d6f88)}
.hero__handshake{position:absolute;left:300px;top:0;width:270px;height:170px;background:linear-gradient(160deg,#b8cfe0,#e6eef4 55%,#7d93ad)}
.hero__pill{position:absolute;left:140px;top:126px;width:300px;height:76px;border-radius:18px;background:var(--navy);border:3px solid #fff;color:#fff;text-align:center;font-size:19px;font-weight:700;line-height:1.3;padding-top:10px;box-shadow:0 4px 12px rgba(0,0,0,.2)}
.hero__pill .refer{color:var(--sky)}
.hero__pill .earn{color:var(--yellow)}
.tiles{position:absolute;display:flex;gap:3px}
.tiles span{width:24px;height:26px;background:#dbeaf0;border-radius:3px;box-shadow:0 2px 3px rgba(0,0,0,.25);font-size:18px;font-weight:700;color:#c1434b;text-align:center;line-height:26px}
.tiles--cash{left:112px;top:222px}
.tiles--flow{left:372px;top:192px}

/* how it works */
.how__title{position:absolute;left:0;right:0;top:286px;text-align:center;font-size:30px;font-weight:800;letter-spacing:.02em;color:var(--navy);background:transparent;z-index:2}
.how__title span{background:#fff;padding:0 12px}
.how__frame{position:absolute;left:38px;top:304px;width:494px;height:290px;border:1.5px solid var(--line);border-radius:14px}
.steps{position:absolute;left:38px;top:318px;width:494px;height:270px;display:flex}
.step{flex:1;position:relative;text-align:center;padding:0 10px}
.step + .step{border-left:1px solid var(--line)}
.step__num{position:absolute;left:0;right:0;top:-6px;font-size:108px;font-weight:900;color:var(--numeral);line-height:1}
.step__icon{position:relative;margin:18px auto 0;width:54px;height:54px}
.step__head{position:relative;font-size:9.5px;font-weight:800;line-height:1.2;margin-top:26px;text-transform:uppercase}
.step__text{position:relative;font-size:9px;font-weight:500;line-height:1.3;margin-top:5px}
.step__text .hl{color:var(--sky)}
.step__photo{position:absolute;left:14px;right:14px;bottom:8px;height:76px}
.photo--pipe{background:linear-gradient(135deg,#6b6f74,#e9ecef 45%,#bfc4c8)}
.photo--house{background:linear-gradient(180deg,#cfd9e2,#8d9b7f 70%,#5e6e54)}
.photo--sky{background:linear-gradient(180deg,#3d86c9,#cfe3f3 80%)}
.tagline{position:absolute;left:0;right:0;top:604px;text-align:center;font-size:14px;font-weight:700;line-height:1.35;color:var(--navy)}
.tagline .free{color:var(--yellow)}

/* front side */
.front__money{position:absolute;right:0;top:0;width:300px;height:340px;background:linear-gradient(135deg,#f4f5f2,#dfe6dc 50%,#ecefe9);opacity:.85}
.headline{position:absolute;left:0;right:0;top:38px;text-align:center;font-weight:900;color:var(--navy);line-height:.95}
.headline__line{display:block;font-size:50px;letter-spacing:.02em}
.headline__cash{display:block;font-size:104px;letter-spacing:.01em;background:linear-gradient(180deg,var(--yellow),var(--amber));-webkit-background-clip:text;background-clip:text;color:transparent;filter:drop-shadow(4px 4px 0 var(--navy));margin-top:4px}
.offer{position:absolute;left:95px;top:266px;width:380px;height:76px;border-radius:20px;background:var(--navy);display:flex;align-items:center;padding-left:14px;color:#fff}
.offer__coin{width:54px;height:54px;flex:none}
.offer__text{margin-left:14px;font-size:21px;font-weight:700;line-height:1.15}
.ribbon{position:absolute;left:36px;top:356px;width:500px;height:30px;background:var(--navy);color:#fff;font-size:13px;font-weight:700;letter-spacing:.14em;display:flex;align-items:center;justify-content:center;padding-left:24px}
.ribbon__badge{position:absolute;left:-14px;top:-8px;width:46px;height:46px}
.benefits{position:absolute;left:40px;right:40px;top:402px;display:flex;justify-content:space-between}
.benefit{width:110px;text-align:center}
.benefit svg{width:40px;height:40px;display:block;margin:0 auto}
.benefit__label{font-size:12px;font-weight:600;line-height:1.2;margin-top:6px}
.front__kitchen{position:absolute;left:40px;right:40px;top:482px;height:170px;background:linear-gradient(180deg,#f1f3f4,#dde2e6 60%,#c7ccd0)}
</style>
</head>
<body>

<!-- Back side -->
<section class="flyer flyer--back">
  <div class="hero">
    <div class="hero__money" role="img" aria-label="Spread of dollar bills"></div>
    <div class="hero__team" role="img" aria-label="Group of smiling professionals giving thumbs up"></div>
    <div class="hero__handshake" role="img" aria-label="Business handshake in front of an office building"></div>
    <div class="hero__pill">The more you <span class="refer">REFER</span><br>the more you <span class="earn">EARN</span></div>
    <div class="tiles tiles--cash"><span>C</span><span>A</span><span>S</span><span>H</span></div>
    <div class="tiles tiles--flow"><span>F</span><span>L</span><span>O</span><span>W</span></div>
  </div>

  <h2 class="how__title"><span>HOW IT WORKS</span></h2>
  <div class="how__frame"></div>
  <div class="steps">
    <div class="step">
      <div class="step__num">1</div>
      <svg class="step__icon" viewBox="0 0 54 54" fill="none" stroke="#1c3f7c" stroke-width="1.8" stroke-linecap="round" stroke-linejoin="round">
        <path d="M14 27 L27 16 L40 27"/><path d="M17 25 V38 H37 V25"/><path d="M24 38 V30 H30 V38"/>
        <path d="M8 22 A20 20 0 0 1 44 14"/><path d="M46 32 A20 20 0 0 1 10 40"/><path d="M44 8 V14 H38"/><path d="M10 46 V40 H16"/>
      </svg>
      <div class="step__head">Refer flood, water<br>and mold damage</div>
      <div class="step__text">Call, book online, or<br><span class="hl">text us directly</span></div>
      <div class="step__photo photo--pipe" role="img" aria-label="Leaking pipe under a sink"></div>
    </div>
    <div class="step">
      <div class="step__num">2</div>
      <svg class="step__icon" viewBox="0 0 54 54" fill="none" stroke="#1c3f7c" stroke-width="1.8" stroke-linecap="round" stroke-linejoin="round">
        <rect x="10" y="6" width="26" height="36" rx="2"/>
        <path d="M15 14 l2 2 l3 -3 M23 15 H31 M15 22 l2 2 l3 -3 M23 23 H31 M15 30 l2 2 l3 -3 M23 31 H28"/>
        <circle cx="40" cy="40" r="6"/><circle cx="40" cy="40" r="2.2"/>
        <path d="M40 31 V34 M40 46 V49 M31 40 H34 M46 40 H49 M34 34 l2 2 M44 44 l2 2 M46 34 l-2 2 M36 44 l-2 2"/>
      </svg>
      <div class="step__head">We take care of<br>everything</div>
      <div class="step__text"><span class="hl">FREE evaluations</span><br>Insurance claims<br>&amp; Professional service.</div>
      <div class="step__photo photo--house" role="img" aria-label="Inspector with a clipboard in front of a house"></div>
    </div>
    <div class="step">
      <div class="step__num">3</div>
      <svg class="step__icon" viewBox="0 0 54 54" fill="none" stroke="#1c3f7c" stroke-width="1.8" stroke-linecap="round" stroke-linejoin="round">
        <rect x="4" y="15" width="46" height="24" rx="2"/><rect x="8" y="19" width="38" height="16" rx="1"/>
        <circle cx="27" cy="27" r="6.5"/><path d="M29 24 h-3 a1.5 1.5 0 0 0 0 3 h2 a1.5 1.5 0 0 1 0 3 h-3 M27 22.5 v1.5 M27 30 v1.5"/>
      </svg>
      <div class="step__head">Get paid to<br>share</div>
      <div class="step__text"><span class="hl">$500 minimum or 10%<br>of the invoice</span> within<br>48 hours of final payment</div>
      <div class="step__photo photo--sky" role="img" aria-label="Yellow road sign reading get paid to share against a blue sky"></div>
    </div>
  </div>

  <p class="tagline">We Schedule <span class="free">FREE</span> estimate. &nbsp;If Approved, you Get <span class="free">Paid</span>.<br>Everybody benefits from Referrals.</p>

  <footer class="contact-bar">
    <div class="contact-bar__label">CALL TEXT OR BOOK ONLINE</div>
    <div class="contact-bar__phone">858-471-6093</div>
    <div class="contact-bar__url">BrightlaneRenovate.com</div>
  </footer>
</section>

<!-- Front side -->
<section class="flyer flyer--front">
  <div class="front__money" role="img" aria-label="Soft-focus stack of dollar bills"></div>

  <h1 class="headline">
    <span class="headline__line">EARN</span>
    <span class="headline__line">UNLIMITED</span>
    <span class="headline__cash">CASH</span>
  </h1>

  <div class="offer">
    <svg class="offer__coin" viewBox="0 0 54 54">
      <circle cx="27" cy="27" r="26" fill="#f5c518"/>
      <circle cx="27" cy="27" r="20" fill="none" stroke="#e0a313" stroke-width="2"/>
      <text x="27" y="37" text-anchor="middle" font-family="Montserrat, sans-serif" font-weight="900" font-size="28" fill="#1c3f7c">$</text>
    </svg>
    <div class="offer__text">$500 minimum OR<br>10% per referral</div>
  </div>

  <div class="ribbon">
    <svg class="ribbon__badge" viewBox="0 0 46 46">
      <circle cx="23" cy="23" r="21" fill="#e8f1f8" stroke="#1c3f7c" stroke-width="3"/>
      <path d="M14 23 l6 6 l12 -12" fill="none" stroke="#1c3f7c" stroke-width="4" stroke-linecap="round" stroke-linejoin="round"/>
    </svg>
    PREMIER PARTNER PROGRAM
  </div>

  <div class="benefits">
    <div class="benefit">
      <svg viewBox="0 0 40 40" fill="none" stroke="#1c3f7c" stroke-width="1.8" stroke-linecap="round" stroke-linejoin="round">
        <path d="M20 3 l4 3 5 -1 2 5 5 2 -1 5 3 4 -3 4 1 5 -5 2 -2 5 -5 -1 -4 3 -4 -3 -5 1 -2 -5 -5 -2 1 -5 -3 -4 3 -4 -1 -5 5 -2 2 -5 5 1z"/>
        <path d="M14 20 l4 4 l8 -8"/>
      </svg>
      <div class="benefit__label">Guaranteed<br>Payout</div>
    </div>
    <div class="benefit">
      <svg viewBox="0 0 40 40" fill="none" stroke="#1c3f7c" stroke-width="1.8" stroke-linecap="round" stroke-linejoin="round">
        <path d="M8 3 H24 L30 9 V36 H8 Z"/><path d="M24 3 V9 H30"/><path d="M12 14 H24 M12 19 H22"/>
        <circle cx="24" cy="27" r="5"/><path d="M28 31 L34 37"/>
      </svg>
      <div class="benefit__label">FREE<br>Evaluation</div>
    </div>
    <div class="benefit">
      <svg viewBox="0 0 40 40" fill="none" stroke="#1c3f7c" stroke-width="1.8" stroke-linecap="round" stroke-linejoin="round">
        <path d="M5 5 H35 V35 H5 Z"/><path d="M5 18 H16 V5 M22 5 V14 H35 M16 35 V26 H28 V35 M22 18 V26"/>
      </svg>
      <div class="benefit__label">Affordable<br>Solutions</div>
    </div>
    <div class="benefit">
      <svg viewBox="0 0 40 40" fill="none" stroke="#1c3f7c" stroke-width="1.8" stroke-linecap="round" stroke-linejoin="round">
        <path d="M3 14 L10 12 L16 22 L10 26 Z"/><path d="M37 14 L30 12 L24 22 L30 26 Z"/>
        <path d="M13 17 L20 13 L24 15 L28 14"/><path d="M18 16 L23 21 a2 2 0 0 1 -3 3 L16 20"/>
        <path d="M14 24 L18 28 M17 23 L21 27 a2 2 0 0 0 3 -3"/>
      </svg>
      <div class="benefit__label">Industry<br>Leaders</div>
    </div>
  </div>

  <div class="front__kitchen" role="img" aria-label="Bright modern white kitchen with an island"></div>

  <footer class="contact-bar">
    <div class="contact-bar__label">CALL TEXT OR BOOK ONLINE</div>
    <div class="contact-bar__phone">858-471-6093</div>
    <div class="contact-bar__url">BrightlaneRenovate.com</div>
  </footer>
</section>

</body>
</html>
```